Flyer für Anbieter von Haushaltshilfen und Alltagsbegleitern für Privathaushalte
Zielgruppe
Wir bieten Haushaltshilfen und Alltagsbegleiter für Privathaushalte an. Unsere Hauptkundenklientel sind Pflegebedürftige Menschen denen eine Haushaltshilfe von der Pflegekasse zusteht. Weitere Kunden sind Familien und/oder Singlehaushalte, die eine Haushaltfshilfe benötigen.
Aufgabenstellung
- Erstellung neues Design eines Flyers 105x210
- Es sollen hauptsächlich unsere Logofarben Rot und Grau verwendet werden

```html
<!DOCTYPE html>
<html lang="de">
<head>
<meta charset="utf-8">
<title>Helferhand Flyer</title>
<link rel="stylesheet" href="https://fonts.googleapis.com/css2?family=Poppins:wght@500;600;700;800&family=Open+Sans:wght@400;700&display=swap">
<style>
  :root {
    --red: #c51f33;
    --red-dark: #a81c2b;
    --red-deep: #b41d2e;
    --grey: #4a4a4a;
    --grey-light: #d9d7d4;
    --white: #ffffff;
    --ink: #1f1f1f;
  }
  * { margin: 0; padding: 0; box-sizing: border-box; }
  html, body { width: 1200px; height: 2400px; overflow: hidden; }
  body { background: var(--red-dark); font-family: "Open Sans", sans-serif; position: relative; }

  .flyer { position: absolute; top: 680px; width: 520px; height: 1040px; overflow: hidden; box-shadow: 0 6px 18px rgba(0,0,0,.25); }
  .flyer--front { left: 50px; background: var(--red); }
  .flyer--back { left: 630px; background: var(--red); }

  .photo { position: absolute; left: 0; top: 0; width: 520px; height: 870px;
    background: linear-gradient(180deg, #dcd9d6 0%, #cfcfc6 18%, #b9c2a4 40%, #a8ae94 55%, #9a9c93 72%, #6f7680 100%); }

  .brand { position: absolute; top: 42px; left: 48px; display: flex; align-items: center; gap: 10px; }
  .brand__dot { width: 46px; height: 46px; border-radius: 50%; border: 4px solid var(--red); }
  .brand__name { font-family: "Poppins", sans-serif; font-weight: 700; font-size: 27px; letter-spacing: .5px; color: var(--red); line-height: 1; }
  .brand__sub { font-family: "Poppins", sans-serif; font-weight: 600; font-size: 9.5px; color: var(--red); letter-spacing: .4px; margin-top: 3px; }
  .brand__rule { position: absolute; top: 64px; left: 292px; width: 176px; height: 1px; background: var(--grey); }
  .flyer--back .brand__dot { border-color: var(--white); }
  .flyer--back .brand__name, .flyer--back .brand__sub { color: var(--white); }
  .flyer--back .brand__rule { background: rgba(255,255,255,.35); left: 290px; width: 180px; }

  .headline { position: absolute; left: 48px; top: 122px; width: 440px; font-family: "Poppins", sans-serif; font-weight: 800; font-size: 58px; line-height: 62px; color: var(--red); letter-spacing: -.5px; }
  .intro { position: absolute; left: 48px; top: 330px; width: 290px; font-size: 13.5px; line-height: 24.5px; color: var(--ink); }
  .intro b { font-weight: 700; }

  .badge { position: absolute; left: 36px; top: 470px; display: flex; align-items: center; }
  .badge__circle { position: relative; z-index: 1; width: 72px; height: 72px; border-radius: 50%; background: var(--red); color: var(--white); text-align: center; font-family: "Poppins", sans-serif; display: flex; flex-direction: column; justify-content: center; }
  .badge__small { font-size: 10px; line-height: 11px; }
  .badge__amount { font-size: 25px; font-weight: 600; line-height: 24px; }
  .badge__amount sup { font-size: 9px; }
  .badge__pill { margin-left: -14px; background: var(--red); color: var(--white); border-radius: 0 8px 8px 0; padding: 7px 12px 7px 24px; font-family: "Poppins", sans-serif; font-size: 10px; line-height: 11px; }

  .bottom-band { position: absolute; left: 0; top: 860px; width: 520px; height: 180px; background: var(--red-deep); }
  .offer-panel { position: absolute; left: 26px; top: 712px; width: 466px; height: 328px; background: var(--red); border-radius: 28px 28px 0 0; }
  .offer-panel__text { position: absolute; left: 22px; top: 22px; width: 420px; font-size: 13.5px; line-height: 26px; color: var(--white); }
  .rule-short { position: absolute; height: 1px; width: 56px; background: rgba(255,255,255,.55); }
  .cta { position: absolute; left: 48px; top: 880px; font-family: "Poppins", sans-serif; font-weight: 600; font-size: 21px; color: var(--white); line-height: 34px; }
  .cta__phone { display: flex; align-items: center; gap: 8px; font-weight: 700; }
  .web { position: absolute; left: 48px; top: 980px; font-family: "Poppins", sans-serif; font-size: 12px; color: var(--white); }
  .web-rule { position: absolute; top: 988px; right: 48px; width: 44px; height: 1px; background: rgba(255,255,255,.6); }

  .back-headline { position: absolute; left: 46px; top: 172px; width: 440px; font-family: "Poppins", sans-serif; font-weight: 800; font-size: 52px; line-height: 62px; color: var(--white); }
  .back-text { position: absolute; left: 48px; top: 556px; width: 400px; font-size: 13.5px; line-height: 24.5px; color: var(--white); }
  .back-text p + p { margin-top: 8px; }
  .contact { position: absolute; left: 48px; top: 830px; font-family: "Poppins", sans-serif; color: var(--white); }
  .contact__title { font-weight: 600; font-size: 21px; margin-bottom: 8px; }
  .contact__row { display: flex; font-weight: 600; font-size: 19px; line-height: 25px; }
  .contact__label { width: 122px; }
</style>
</head>
<body>
  <section class="flyer flyer--front">
    <div class="photo" role="img" aria-label="Foto: junge Haushaltshilfe und ältere Dame sitzen mit gefalteter Wäsche in einem hellen Wohnzimmer"></div>
    <div class="brand">
      <span class="brand__dot"></span>
      <div><div class="brand__name">HELFERHAND</div><div class="brand__sub">HAUSHALTSHILFEN &amp; MEHR</div></div>
    </div>
    <span class="brand__rule"></span>
    <h1 class="headline">Verschenken Sie nicht Ihr Geld!!</h1>
    <p class="intro">Nutzen Sie Ihre <b>Verhinderungspflege</b> ab dem Pflegegrad 2 bis zum 31.12.2024, sonst verfällt Ihr Anspruch. Denken Sie auch an Ihren <b>Entlastungsbetrag</b> ab Pflegegrad 1.</p>
    <div class="badge">
      <div class="badge__circle"><span class="badge__small">mind.</span><span class="badge__amount">125<sup>€</sup></span><span class="badge__small">mtl.</span></div>
      <div class="badge__pill">für Haushaltshilfe<br>ab Pflegegrad 1</div>
    </div>
    <div class="bottom-band"></div>
    <div class="offer-panel">
      <p class="offer-panel__text">Als anerkannter und zugelassener Dienstleister für Haushaltsnahe Services, können wir unsere Leistungen über den Entlastungsbetrag oder der Verhinderungs­pflege direkt mit Ihrer Pflegekasse abrechnen!</p>
    </div>
    <span class="rule-short" style="left:48px;top:858px"></span>
    <div class="cta">
      <div>Jetzt Termin vereinbaren!</div>
      <div class="cta__phone">
        <svg width="18" height="18" viewBox="0 0 24 24" aria-hidden="true"><path fill="#fff" d="M6.6 10.8c1.4 2.8 3.8 5.1 6.6 6.6l2.2-2.2c.3-.3.7-.4 1-.2 1.1.4 2.3.6 3.6.6.6 0 1 .4 1 1V20c0 .6-.4 1-1 1C10.6 21 3 13.4 3 4c0-.6.4-1 1-1h3.5c.6 0 1 .4 1 1 0 1.3.2 2.5.6 3.6.1.3 0 .7-.2 1z"/></svg>
        0711 12 34 56 78
      </div>
    </div>
    <div class="web">www.helferhand.de</div>
    <span class="web-rule"></span>
  </section>

  <section class="flyer flyer--back">
    <div class="brand">
      <span class="brand__dot"></span>
      <div><div class="brand__name">HELFERHAND</div><div class="brand__sub">HAUSHALTSHILFEN &amp; MEHR</div></div>
    </div>
    <span class="brand__rule"></span>
    <h2 class="back-headline">Sie sind pflegebeürftig und benötigen Hilfe im Haushalt?</h2>
    <span class="rule-short" style="left:48px;top:512px"></span>
    <div class="back-text">
      <p>Um Älteren oder beeinträchtigten Menschen ein Leben in ihrem sozialen Umfeld zu ermöglichen, bedarf es der Unterstützung im Alltag. Die dabei täglich anfallenden Aufgaben des Haushalts können oft belastend sein und die Pflege der betroffenen Personen erschweren.</p>
      <p>Um sie zu entlasten, bieten wir Ihnen bedarfsorientierte Hilfe rund um den Haushalt an. Mit unserem breiten Spektrum an Services möchten wir Sie beim bewältigen des Alltags unterstützen.</p>
    </div>
    <div class="contact">
      <div class="contact__title">Jetzt kostenlos beraten lassen!</div>
      <div class="contact__row"><span class="contact__label">Festnetz</span><span>: 0711 12 34 56 78</span></div>
      <div class="contact__row"><span class="contact__label">24/7 Mobil</span><span>: 0176 98 76 54 32</span></div>
      <div class="contact__row"><span class="contact__label">Email</span><span>: info@helferhand.de</span></div>
    </div>
    <div class="web">www.helferhand.de</div>
    <span class="web-rule"></span>
  </section>
</body>
</html>
```